Simple landing page for Brambles cookbook

I need a one page landingpage where customers can order the cookbook.
This is a cookbook of a collection of recipes from our deli that we used to run.
I need a landing page where customers can come and order the book. I also need it coded. I already have the domain through hostwell.
I can send the file of the book through wetransfer. It's too big to upload here. Just so you get the feel that I am looking for.
I attached a simple text as an introduction to the page. But I am open to any suggestions. I want it all to be about the experience that we are sharing the recipes with everybody and that it's for sale. The book is $29.99, shipping included.
Customers have to be able to click and buy the book from it.

Coding

Coded - Design and coding required

Number of Pages Required

1 page

Font styles to use
Sans Serif

Requirements
Must have
• Same colors as the cookbook

```html
<!DOCTYPE html>
<html lang="en">
<head>
<meta charset="utf-8">
<title>Brambles Cookbook</title>
<link href="https://fonts.googleapis.com/css2?family=Bebas+Neue&family=Roboto+Condensed:wght@700&family=Quicksand:wght@500;600&display=swap" rel="stylesheet">
<style>
  :root {
    --brown-dark: #3b230f;
    --brown: #5a3511;
    --brown-mid: #6b4320;
    --green: #7fa23a;
    --green-light: #9cbf52;
    --blush: #f8dfd2;
    --blush-light: #fbeee6;
    --ink: #3a2412;
    --white: #ffffff;
    --grey-text: #555555;
  }
  * { margin: 0; padding: 0; box-sizing: border-box; }
  html, body { width: 701px; height: 1200px; overflow: hidden; background: var(--white); }
  body { position: relative; font-family: "Quicksand", sans-serif; color: var(--ink); }

  .backdrop { position: absolute; left: 0; top: 0; width: 701px; height: 1200px; }

  .hero-photo { position: absolute; left: 0; top: 0; width: 701px; height: 345px;
    background: linear-gradient(120deg, #4a3218 0%, #5e4226 40%, #3d2610 70%, #6d5a46 100%); }

  .brand { position: absolute; left: 85px; top: 12px; display: flex; align-items: center; gap: 6px; }
  .brand-dot { width: 14px; height: 14px; border-radius: 50%; background: var(--green); }
  .brand-name { font-family: "Quicksand", sans-serif; font-weight: 600; font-size: 20px; color: var(--white); }

  .hero-title { position: absolute; left: 85px; top: 108px; width: 300px;
    font-family: "Bebas Neue", sans-serif; font-size: 22.5px; line-height: 30px; letter-spacing: 0.6px; color: var(--white); }

  .includes { position: absolute; left: 85px; top: 207px; font-size: 10.5px; font-weight: 600; letter-spacing: 1px; color: var(--white); }
  .includes .count { color: var(--green); font-size: 12.5px; }

  .categories { position: absolute; left: 83px; top: 226px; display: flex; gap: 11px; list-style: none; }
  .categories li { display: flex; align-items: center; gap: 5px; font-size: 8px; letter-spacing: 0.6px; color: var(--white); }
  .cat-icon { width: 17px; height: 17px; border-radius: 50%; background: var(--white); display: flex; align-items: center; justify-content: center; }

  .btn { position: absolute; display: flex; align-items: center; justify-content: center; width: 89px; height: 22px; border-radius: 11px;
    background: var(--green); color: var(--white); text-decoration: none;
    font-family: "Roboto Condensed", sans-serif; font-weight: 700; font-size: 9.5px; letter-spacing: 1.2px; }
  .btn-hero { left: 85px; top: 256px; }
  .btn-offer { left: 451px; top: 895px; box-shadow: 0 3px 8px rgba(0,0,0,0.18); }

  .book-hero { position: absolute; left: 440px; top: 44px; width: 173px; height: 277px;
    background: linear-gradient(180deg, #f6f6f6 0%, #f0f0f0 45%, #a99375 62%, #555a55 80%, #f2f2f2 100%);
    box-shadow: 6px 6px 14px rgba(0,0,0,0.25); }

  .price-badge { position: absolute; width: 70px; height: 70px; }
  .price-badge .amount { position: absolute; left: 0; top: 17px; width: 70px; text-align: center;
    font-family: "Roboto Condensed", sans-serif; font-weight: 700; font-size: 18px; color: var(--white); }
  .price-badge .amount small { font-size: 9px; }
  .price-badge .ship { position: absolute; left: 14px; top: 43px; display: flex; align-items: center; gap: 3px;
    font-size: 5px; line-height: 6px; color: var(--white); }
  .badge-hero { left: 405px; top: 104px; }
  .badge-offer { left: 461px; top: 715px; }

  .story-card { position: absolute; left: 85px; top: 396px; width: 532px; height: 224px; border-radius: 8px; overflow: hidden;
    display: flex; box-shadow: 0 6px 16px rgba(0,0,0,0.22); }
  .story-photo { width: 275px; height: 100%;
    background: radial-gradient(ellipse at 45% 45%, #b8692a 0%, #9a5a2a 35%, #c08558 60%, #d8d0c8 78%, #8c5a32 100%); }
  .story-text { flex: 1; background: linear-gradient(180deg, var(--brown-dark), var(--brown));
    padding: 38px 18px 0 32px; font-family: "Roboto Condensed", sans-serif; font-weight: 700; font-size: 13.6px; line-height: 20.5px; letter-spacing: 0.9px; color: var(--white); }

  .books-offer { position: absolute; left: 40px; top: 674px; width: 312px; height: 317px;
    background: linear-gradient(180deg, #e0e0e0 0%, #cfcfcf 40%, #8a7a66 58%, #3f4442 78%, #d4d4d4 100%);
    clip-path: polygon(0 27%, 57% 0, 60% 9%, 100% 9%, 100% 88%, 70% 88%, 20% 100%); }

  .offer-title { position: absolute; left: 370px; top: 795px; width: 250px; text-align: center;
    font-family: "Roboto Condensed", sans-serif; font-weight: 700; font-size: 27px; line-height: 30px; letter-spacing: 2px; color: var(--ink); }
  .offer-sub { position: absolute; left: 370px; top: 859px; width: 250px; text-align: center; font-size: 8px; line-height: 11px; letter-spacing: 0.5px; font-weight: 500; color: var(--ink); }

  .quote-card { position: absolute; left: 85px; top: 1024px; width: 532px; height: 128px; border-radius: 8px;
    background: linear-gradient(180deg, var(--brown-dark), var(--brown)); }
  .quote-mark { position: absolute; left: 333px; top: 1006px; width: 35px; height: 35px; border-radius: 50%; background: var(--green);
    box-shadow: 0 0 14px rgba(220,130,130,0.45); display: flex; align-items: center; justify-content: center; }
  .quote-text { position: absolute; left: 140px; top: 1062px; width: 422px; text-align: center;
    font-size: 10.7px; line-height: 17.3px; letter-spacing: 1px; font-weight: 500; color: var(--white); }

  .footer { position: absolute; left: 0; top: 1176px; width: 701px; text-align: center; font-size: 8px; font-weight: 500; color: var(--grey-text); }
</style>
</head>
<body>

<div class="hero-photo" role="img" aria-label="Photo of the deli storefront interior with its overhead sign"></div>

<svg class="backdrop" viewBox="0 0 701 1200" aria-hidden="true">
  <path d="M0 345 L0 300 C100 345 240 340 440 280 C550 250 640 262 701 282 L701 345 Z" fill="#ffffff"/>
  <path d="M26 295 C90 325 140 340 172 345 L120 345 C80 330 50 315 26 295 Z" fill="#ffffff"/>
  <path d="M0 604 C120 720 260 760 420 752 C540 745 640 710 701 690 L701 962 L520 962 C600 950 660 915 690 885 C600 930 480 950 360 935 C220 915 90 900 0 898 Z" fill="var(--blush)"/>
  <path d="M701 720 C640 735 560 740 480 730 L701 962 Z" fill="var(--blush-light)" opacity="0.7"/>
</svg>

<div class="brand">
  <span class="brand-dot"></span>
  <span class="brand-name">Brambles</span>
</div>

<h1 class="hero-title">It's finally here! The Brambles cookbook with all your favourite recipes</h1>

<p class="includes">BOOK INCLUDES <span class="count">28 RECIPES:</span></p>

<ul class="categories">
  <li><span class="cat-icon"><svg width="10" height="8" viewBox="0 0 10 8"><path d="M1 6 L5 1 L9 6 Z" fill="none" stroke="#7fa23a" stroke-width="1"/></svg></span>Sandwiches</li>
  <li><span class="cat-icon"><svg width="10" height="8" viewBox="0 0 10 8"><path d="M1 3 H9 L7.5 7 H2.5 Z" fill="none" stroke="#7fa23a" stroke-width="1"/></svg></span>Sauces</li>
  <li><span class="cat-icon"><svg width="10" height="8" viewBox="0 0 10 8"><path d="M1 4 C1 1 9 1 9 4 Z M1 5.5 H9 M1.5 7 H8.5" fill="none" stroke="#7fa23a" stroke-width="1"/></svg></span>Burgers</li>
</ul>

<a class="btn btn-hero" href="#order">ORDER NOW</a>

<div class="book-hero" role="img" aria-label="Brambles cookbook hardcover with a chalkboard order sign on the cover"></div>

<div class="price-badge badge-hero">
  <svg width="70" height="70" viewBox="0 0 70 70" aria-hidden="true"><polygon points="35,0 44,6 55,5 58,16 68,22 64,33 68,44 58,51 55,62 44,62 35,70 26,62 15,62 12,51 2,44 6,33 2,22 12,16 15,5 26,6" fill="#7fa23a"/></svg>
  <div class="amount"><small>$</small>29.99</div>
  <div class="ship"><svg width="12" height="7" viewBox="0 0 12 7"><rect x="0.5" y="0.5" width="7" height="4.5" fill="none" stroke="#fff" stroke-width="0.8"/><path d="M7.5 2 H10 L11.5 4 V5 H7.5" fill="none" stroke="#fff" stroke-width="0.8"/><circle cx="2.5" cy="6" r="0.9" fill="#fff"/><circle cx="9" cy="6" r="0.9" fill="#fff"/></svg><span>Free<br>Shipping</span></div>
</div>

<section class="story-card">
  <div class="story-photo" role="img" aria-label="Photo of a salted pretzel sandwich with cheese on a white plate"></div>
  <p class="story-text">We can't open another Brambles restaurant but we can offer you this compilation of our best recipies for you to make and enjoy at home. Storefront picture beside it or something like that.</p>
</section>

<div class="books-offer" role="img" aria-label="Two Brambles cookbooks stacked, showing the front covers"></div>

<div class="price-badge badge-offer">
  <svg width="70" height="70" viewBox="0 0 70 70" aria-hidden="true"><polygon points="35,0 44,6 55,5 58,16 68,22 64,33 68,44 58,51 55,62 44,62 35,70 26,62 15,62 12,51 2,44 6,33 2,22 12,16 15,5 26,6" fill="#7fa23a"/></svg>
  <div class="amount"><small>$</small>29.99</div>
  <div class="ship"><svg width="12" height="7" viewBox="0 0 12 7"><rect x="0.5" y="0.5" width="7" height="4.5" fill="none" stroke="#fff" stroke-width="0.8"/><path d="M7.5 2 H10 L11.5 4 V5 H7.5" fill="none" stroke="#fff" stroke-width="0.8"/><circle cx="2.5" cy="6" r="0.9" fill="#fff"/><circle cx="9" cy="6" r="0.9" fill="#fff"/></svg><span>Free<br>Shipping</span></div>
</div>

<h2 class="offer-title">FAVORITE RECIPES<br>IN ONE BOOK</h2>
<p class="offer-sub">We Truly Hope You Will Enjoy Making These Sandwiches Just As Much As We Did.</p>
<a class="btn btn-offer" id="order" href="#order">ORDER NOW</a>

<section class="quote-card"></section>
<div class="quote-mark"><svg width="16" height="12" viewBox="0 0 16 12" aria-hidden="true"><circle cx="4" cy="4" r="3" fill="none" stroke="#fff" stroke-width="1.5"/><path d="M7 4 C7 8 5 10 2 11" fill="none" stroke="#fff" stroke-width="1.5"/><circle cx="12" cy="4" r="3" fill="none" stroke="#fff" stroke-width="1.5"/><path d="M15 4 C15 8 13 10 10 11" fill="none" stroke="#fff" stroke-width="1.5"/></svg></div>
<p class="quote-text">We can't open another Brambles, but we can offer you this collection of our recipes for you to try out at home with your family and friends.</p>

<footer class="footer">Copyright 2022. Rowan Ellis | All Rights Reserved</footer>

</body>
</html>
```